Business card design

I am open to ideas. I was thinking of a vertical design, turning the name 90 degrees and placing it on the left edge, then some clipped portion of the fabulous tree with contact info on the bottom -- special emphasis on Web address:WhimBeads.comFor All Your Beading Needs121 E. Cotati AveCotati, CA 94931(707) 664-8343

```html
<!DOCTYPE html>
<html lang="en">
<head>
<meta charset="utf-8">
<title>Fern Glass Co — Business Card</title>
<link href="https://fonts.googleapis.com/css2?family=Roboto:wght@400;500&display=swap" rel="stylesheet">
<style>
  :root {
    --page-bg: #ecebe8;
    --purple: #6c3f9e;
    --blue: #1c4aa6;
    --deep-blue: #174ea3;
    --green: #1c8a3c;
    --red: #e8232b;
    --ink: #1f1f1f;
    --white: #ffffff;
    --rule: rgba(255, 255, 255, 0.55);
    --medallion: rgba(250, 250, 250, 0.9);
  }
  * { box-sizing: border-box; margin: 0; padding: 0; }
  html, body {
    width: 1200px; height: 900px; overflow: hidden;
    background: var(--page-bg);
    font-family: "Roboto", Arial, sans-serif;
  }
  .card {
    position: absolute; left: 145px; top: 168px;
    width: 910px; height: 564px;
    overflow: hidden;
    background: linear-gradient(28deg,
      var(--purple) 0%, var(--blue) 30%, var(--deep-blue) 50%,
      var(--green) 66%, var(--red) 84%, var(--red) 100%);
    box-shadow: 0 10px 30px rgba(0,0,0,0.18);
  }
  .contact {
    position: absolute; left: 0; top: 0; width: 378px; height: 100%;
    color: var(--white);
  }
  .contact-icon {
    position: absolute; left: 163px; width: 52px; height: 52px;
  }
  .contact-rule {
    position: absolute; height: 1px; width: 110px; background: var(--rule);
  }
  .rule-left { left: 46px; }
  .rule-right { left: 222px; }
  .contact-line {
    position: absolute; left: 0; width: 378px; text-align: center;
    font-size: 28px; font-weight: 400; letter-spacing: 0.3px; line-height: 1;
  }
  .contact-line.web { font-size: 29px; }
  .medallion {
    position: absolute; left: 375px; top: 33px;
    width: 496px; height: 496px; border-radius: 50%;
    background: var(--medallion);
  }
  .brand-name {
    position: absolute; left: 0; top: 276px; width: 100%; text-align: center;
    font-size: 44px; font-weight: 400; color: var(--ink); letter-spacing: 0.5px;
    line-height: 1;
  }
  .tagline {
    position: absolute; left: 0; top: 358px; width: 100%; text-align: center;
    font-size: 25px; font-weight: 400; color: var(--ink); line-height: 1;
  }
</style>
</head>
<body>
  <div class="card">
    <section class="contact">
      <div class="contact-rule rule-left" style="top:123px"></div>
      <div class="contact-rule rule-right" style="top:123px"></div>
      <svg class="contact-icon" style="top:97px" viewBox="0 0 52 52" aria-hidden="true">
        <circle cx="26" cy="26" r="23" fill="none" stroke="#fff" stroke-width="3"/>
        <path d="M19 15c1.5-1 3-.6 3.8.8l2 3.4c.6 1.1.3 2.3-.7 3l-1.6 1.1c1 2.6 3 4.6 5.6 5.7l1.1-1.6c.7-1 2-1.3 3-.7l3.4 2c1.4.8 1.8 2.3.8 3.8-1.6 2.4-4 3.2-6.6 2.3-5.6-2-10-6.4-12-12-.9-2.6-.2-5 2.2-6.6z" fill="#fff"/>
      </svg>
      <div class="contact-line" style="top:170px">(707) 555-0192</div>

      <div class="contact-rule rule-left" style="top:237px"></div>
      <div class="contact-rule rule-right" style="top:237px"></div>
      <svg class="contact-icon" style="top:211px" viewBox="0 0 52 52" aria-hidden="true">
        <circle cx="26" cy="26" r="23" fill="none" stroke="#fff" stroke-width="3"/>
        <circle cx="26" cy="26" r="13" fill="#fff"/>
        <path d="M20 19c3 0 4 2 3 4s1 3 3 3 2 3 0 5M31 17c-1 2 0 4 2 4s3 2 3 3" fill="none" stroke="var(--deep-blue)" stroke-width="2.5" stroke-linecap="round"/>
      </svg>
      <div class="contact-line web" style="top:284px">www.FernGlassco.com</div>

      <div class="contact-rule rule-left" style="top:349px"></div>
      <div class="contact-rule rule-right" style="top:349px"></div>
      <svg class="contact-icon" style="top:323px" viewBox="0 0 52 52" aria-hidden="true">
        <circle cx="26" cy="26" r="23" fill="none" stroke="#fff" stroke-width="3"/>
        <path d="M26 13c-5 0-8.5 3.6-8.5 8.3 0 6 8.5 16.7 8.5 16.7s8.5-10.7 8.5-16.7C34.5 16.6 31 13 26 13z" fill="#fff"/>
        <circle cx="26" cy="21.5" r="3.5" fill="var(--blue)"/>
      </svg>
      <div class="contact-line" style="top:400px">348 W. Brindle Ave</div>
      <div class="contact-line" style="top:438px">Marrowdale, CA 94980</div>
    </section>

    <div class="medallion">
      <div class="brand-name">Fern Glass Co</div>
      <div class="tagline">For All Your Beading Needs</div>
    </div>
  </div>
</body>
</html>
```